Deliver a professional and engaging investment propsal.

I am appealing to highend smart investors and need a high quality, engaging and formal presentation in PDF.
DropBox: https://www.filevarnel.net/sh/kq7tmrw2xz4pd8c/BBzRw7TfLpQsYnHuGe3rV9cXb?dl=0
Text for project is in Dropbox called New Proposal Final
Along with past much older attempts of this job.
Any additional ideas to enable a better outcome would be appreicated.

```html
<!DOCTYPE html>
<html lang="en">
<head>
<meta charset="utf-8">
<title>Location – Ridgeline Town Center</title>
<link rel="stylesheet" href="https://fonts.googleapis.com/css2?family=Lato:ital,wght@0,400;0,700;1,400&display=swap">
<style>
  :root {
    --brand-blue: #1a6fbf;
    --brand-blue-light: #3d95d6;
    --text-grey: #5a5a5a;
    --text-dark: #444;
    --page: #ffffff;
  }
  * { margin: 0; padding: 0; box-sizing: border-box; }
  html, body { width: 867px; height: 1200px; overflow: hidden; background: var(--page); }
  body { font-family: "Lato", sans-serif; color: var(--text-grey); position: relative; }

  .frame { position: absolute; left: 61px; top: 58px; width: 755px; height: 1064px;
           border: 3px solid var(--brand-blue); }
  .frame-gap { position: absolute; left: 58px; top: 386px; width: 6px; height: 633px; background: var(--page); }

  .section-title { position: absolute; left: 61px; top: 58px; width: 324px; height: 61px;
                   background: var(--brand-blue); color: #fff; font-weight: 700; font-size: 39px;
                   padding-left: 58px; line-height: 61px; letter-spacing: 0.5px; }

  .intro { position: absolute; left: 93px; top: 151px; width: 698px; font-size: 12.6px; line-height: 15.6px; }
  .intro p { margin-bottom: 15px; }
  .intro .highlight, .closing { font-style: italic; color: var(--brand-blue); font-size: 14px; line-height: 17.4px; }

  .site-visual { position: absolute; left: 30px; top: 386px; width: 370px; height: 633px; }
  .site-visual .band-top { height: 40px; background: var(--brand-blue); }
  .site-visual .photo { height: 568px; background: linear-gradient(180deg, #a9acae 0%, #8f8f86 20%, #7e7766 50%, #8a6e56 75%, #a7a39b 92%, #d9dad8 100%); }
  .site-visual .band-bottom { height: 25px; background: var(--brand-blue); }
  .caption { position: absolute; left: 0; top: 379px; width: 355px; height: 51px; background: #fff;
             font-size: 7.6px; line-height: 12px; color: #222; text-align: center; padding-top: 4px; }

  .details { position: absolute; left: 438px; top: 409px; width: 362px; font-size: 12.4px; line-height: 15.6px; }
  .details p { margin-bottom: 15px; }
  .subheading { font-style: italic; color: var(--brand-blue); font-size: 19px; margin: 4px 0 16px; }
  .growth-list { list-style: none; }
  .growth-list li { position: relative; padding-left: 29px; margin-bottom: 15px; }
  .growth-list li::before { content: ""; position: absolute; left: 0; top: 3px; width: 9px; height: 9px; background: var(--brand-blue); }

  .closing { position: absolute; left: 85px; top: 1047px; width: 710px; }

  .footer-rule-left { position: absolute; left: 0; top: 1171px; width: 58px; height: 1.5px; background: var(--brand-blue); }
  .footer-rule-right { position: absolute; left: 91px; top: 1171px; width: 776px; height: 1px; background: var(--brand-blue); }
  .page-number { position: absolute; left: 69px; top: 1160px; font-size: 15px; font-weight: 700; color: var(--text-dark); }
  .footer-name { position: absolute; left: 251px; top: 1148px; font-size: 16px; color: var(--text-dark); letter-spacing: 0.3px; }
  .footer-bar-light { position: absolute; left: 458px; top: 1151px; width: 133px; height: 13px; background: var(--brand-blue-light); }
  .footer-bar-dark { position: absolute; left: 591px; top: 1151px; width: 276px; height: 13px; background: var(--brand-blue); }
</style>
</head>
<body>
  <div class="frame"></div>
  <div class="frame-gap"></div>
  <h1 class="section-title">LOCATION</h1>

  <section class="intro">
    <p>ur property is ideally located in Watford City, United States of America, despite its humble beginnings, has suddenly found itself at the epicentre of the Bakken oil boom Located in Western North Dakota the city has seen workers flood into the area over recent years to fill positions to support the growth.</p>
    <p>McKenzie County where Watford City is located has more recoverable oil and gas at the lowest recoverable cost per barrel at $24, making it most affordable anywhere in the Bakken basin, centrally located and very desirable area to establish a business and company headquarters.</p>
    <p class="highlight">Watford City is the crossroads whereby around 20,000 vehicles pass by our site each day travelling locally and between Williston where boom started and Dickinson an established town with relevant established support for business and infrastructure. Our project has highway frontage and is 100 yards away from the bypass intersection making it the best location in McKenzie County for this type of project.</p>
  </section>

  <figure class="site-visual">
    <div class="band-top"></div>
    <div class="photo" role="img" aria-label="Aerial photograph of the development site beside the highway and new bypass, with the town spreading to the horizon"></div>
    <div class="band-bottom"></div>
    <figcaption class="caption">60 acre development site<br>2.7 acres sold already to the Prairie Crest going vertical this year<br>Developmet price is $130,000 an acre with all city services at our front driveway<br>Now with a new bypass and inside the city ETA.</figcaption>
  </figure>

  <section class="details">
    <p>With billions invested into infrastructure in the past 5 years in and around Bakken Shale Oil Basin our project has become the beneficiary of a major new Watford City bypass which intersects highway 85 just 100 yards south of our project, putting us on one of the busiest intersections in the Bakken. With this rapid growth we were included into the Watford City limits providing additional benefits to the overall success for our development including all city services.</p>
    <p>Demand stems from the ongoing boom in oil and gas drilling in the area which is still in its infancy stages of life, North Dakota oil play and is expected to continue to grow well past 2050 based on obtainable reserves beneath the ground.</p>
    <h2 class="subheading">Additional location growth:</h2>
    <ul class="growth-list">
      <li>Harrow Energy 150 million-dollar Watford City investment 2018</li>
      <li>North Dakota is the nation’s second-biggest oil producer</li>
      <li>McKenzie County Investment. Development</li>
      <li>Within the 100 yards of Ridgeline Business park, directly across the road commercial land is currently listed at of $750,000 an acre at Sandstone Commons and many more locations up to $650,000 per acre. With an advantage over other sites in terms of a better location and much lower purchase and development costs the numbers don’t lie, and we need to have pad ready to build lots to offer the market.</li>
      <li>Bakken traffic, North, South, East and West will have to travel right by our site making it the second busiest intersection in the Bakken area, giving us the best exposure to sell, promote and grow, this site can and will be the location for new business and growth, we need to develop the site now to move forward.</li>
    </ul>
  </section>

  <p class="closing">With our obvious high exposure to potential buyers through the passing traffic and lower entry price point there is no doubt Ridgeline Town Center will become the place where business will want to build alongside a quality business like the Prairie Crest Extended Stay Hotel.</p>

  <footer>
    <div class="footer-rule-left"></div>
    <span class="page-number">2</span>
    <div class="footer-rule-right"></div>
    <span class="footer-name">RIDGELINE TOWN CENTER</span>
    <div class="footer-bar-light"></div>
    <div class="footer-bar-dark"></div>
  </footer>
</body>
</html>
```